New Business card design to reflect rebrand

I would like a business card design with a good base colour for our new logo and also a placeholder for a profile pic of the card holder. the design needs to be editable to the point that we can easily change the picture of the person and use that design for printmerlo etc. we are looking at a metalic finish business card so will need a good base colour to bring out the finish.

Target Market(s)

prospective customers

Industry/Entity Type

Business

Contact Information for Business Card

I would like one editable design that we can change the name of the card holder and profile picture. The design need to be in a format that be send to printmerlo etc.

Our address is Fenwick Lodge, Copse Lane, Ashbury Vale, GU14 3TP Tel no. 01483 556172

Requirements
Must have
• place holder for a profile pic for the card holder. in AI or preferably PSD format

```html
<!DOCTYPE html>
<html lang="en">
<head>
<meta charset="utf-8">
<title>Larkfield Workplace Services – Business Card</title>
<link rel="stylesheet" href="https://fonts.googleapis.com/css2?family=Source+Sans+3:wght@400;600;700&display=swap">
<style>
  :root {
    --bg-top: #262626;
    --bg-bottom: #060606;
    --card-white: #ffffff;
    --navy: #2f4260;
    --orange: #e8661a;
    --text-grey: #3b4757;
    --photo-light: #e9e9ec;
    --photo-dark: #2a2a3a;
    --metal-light: #f2f2f2;
    --metal-mid: #bdbdbd;
    --metal-dark: #5e5e5e;
    --metal-text: #f7f7f7;
  }
  * { margin: 0; padding: 0; box-sizing: border-box; }
  html, body { width: 1200px; height: 900px; overflow: hidden; }
  body {
    position: relative;
    background: linear-gradient(180deg, var(--bg-top) 0%, #141414 55%, var(--bg-bottom) 100%);
    font-family: "Source Sans 3", "Myriad Pro", sans-serif;
  }
  .card {
    position: absolute;
    top: 306px;
    width: 439px;
    height: 271px;
    border-radius: 10px;
    overflow: hidden;
  }
  .card-front { left: 149px; background: var(--card-white); }
  .card-back {
    left: 608px;
    background: linear-gradient(100deg, var(--metal-light) 0%, #e0e0e0 30%, var(--metal-mid) 60%, var(--metal-dark) 100%);
  }

  .brand-front {
    position: absolute;
    left: 20px;
    top: 60px;
    width: 176px;
    color: var(--navy);
    font-weight: 700;
    text-align: center;
  }
  .brand-name { display: block; font-size: 26px; letter-spacing: 1.6px; line-height: 1; }
  .brand-tag { display: block; font-size: 11px; font-weight: 600; letter-spacing: 2.3px; margin-top: 6px; line-height: 1; }

  .holder-name {
    position: absolute;
    left: 23px;
    top: 126px;
    font-size: 24px;
    font-weight: 600;
    color: var(--navy);
  }
  .holder-name .surname { color: var(--orange); }

  .contact-list {
    position: absolute;
    left: 23px;
    top: 166px;
    list-style: none;
    font-size: 12.5px;
    color: var(--text-grey);
  }
  .contact-list li { display: flex; align-items: center; gap: 6px; height: 19px; }
  .contact-list svg { width: 9px; height: 9px; fill: var(--orange); }

  .address {
    position: absolute;
    left: 23px;
    top: 211px;
    font-size: 12.5px;
    line-height: 18px;
    color: var(--text-grey);
    font-style: normal;
  }

  .profile-photo {
    position: absolute;
    right: 0;
    top: 0;
    width: 203px;
    height: 271px;
    background: linear-gradient(180deg, var(--photo-light) 0%, #c9c3c0 35%, var(--photo-dark) 60%, #1c1c28 100%);
  }

  .brand-back {
    position: absolute;
    left: 92px;
    top: 138px;
    width: 258px;
    color: var(--metal-text);
    font-weight: 700;
    text-align: center;
  }
  .brand-back .brand-name { font-size: 35px; letter-spacing: 3.5px; }
  .brand-back .brand-tag { font-size: 14px; letter-spacing: 3.4px; margin-top: 9px; }
</style>
</head>
<body>
  <section class="card card-front" aria-label="Business card front">
    <div class="brand-front">
      <span class="brand-name">LARKFIELD</span>
      <span class="brand-tag">WORKPLACE SERVICES</span>
    </div>

    <h1 class="holder-name">Daniel <span class="surname">Hurst</span></h1>

    <ul class="contact-list">
      <li>
        <svg viewBox="0 0 10 10" aria-hidden="true"><path d="M2 0.5 L3.6 2.6 L2.8 3.6 Q4 6 6.4 7.2 L7.4 6.4 L9.5 8 L8.4 9.5 Q4.5 9.4 2 6.8 Q0.3 4.5 0.5 1.6 Z"/></svg>
        01483 556172
      </li>
      <li>
        <svg viewBox="0 0 10 10" aria-hidden="true"><path d="M0 2 H10 V8.5 H0 Z M0.6 2.4 L5 5.6 L9.4 2.4 V3.2 L5 6.4 L0.6 3.2 Z" fill-rule="evenodd"/></svg>
        info@larkfield.co.uk
      </li>
    </ul>

    <address class="address">
      Fenwick Lodge, Copse Lane,<br>
      Ashbury Vale, GU14 3TP
    </address>

    <div class="profile-photo" role="img" aria-label="Profile photo of the card holder in a dark suit"></div>
  </section>

  <section class="card card-back" aria-label="Business card back, metallic finish">
    <div class="brand-back">
      <span class="brand-name">LARKFIELD</span>
      <span class="brand-tag">WORKPLACE SERVICES</span>
    </div>
  </section>
</body>
</html>
```